Medical Marihuana Ziplock Bag Mockup Design

We seek skilled and professional designer for medical marihuana ziplock bag packaging design. We need a modern, minimal, clean Design with the name productname: Plomu - Endproduct will be a ziplock bag (see attachment) samples.
Product may but must not contain a cannabis leaf in Design7Logo

Target Market(s)

young audience

Industry/Entity Type

Medical

Logo Text

P L O M U

Font styles to use
Serif
Sans Serif

Colors
9bcb3c
abd037
cadf82
ffc214
fece3e
fee18a
6b449b
886aae
b8a6cd

Requirements
Nice to have
• Can but must not contain a minimal cannabis leaf as abstract sign

```html
<!DOCTYPE html>
<html lang="de">
<head>
<meta charset="utf-8">
<title>Plomu – Medical Marijuana Bag</title>
<link rel="stylesheet" href="https://fonts.googleapis.com/css2?family=Marcellus&family=Oswald:wght@600&family=Nunito+Sans:wght@600&display=swap">
<style>
  :root {
    --green-top: #659a40;
    --green-brand: #6a9d3f;
    --green-pill: #8cc63f;
    --green-light: #93c94a;
    --green-dark: #2d5428;
    --green-deep: #3f6d30;
    --cross: #5f9645;
    --grey-soft: #d8d9dc;
    --white: #ffffff;
    --black: #000000;
  }
  * { margin: 0; padding: 0; box-sizing: border-box; }
  html, body { width: 901px; height: 1200px; overflow: hidden; background: var(--white); }
  .bag {
    position: relative; width: 901px; height: 1200px; overflow: hidden;
    background: linear-gradient(to bottom, var(--white) 0, var(--white) 300px, var(--grey-soft) 451px);
    font-family: "Marcellus", serif;
  }
  .top-band { position: absolute; left: 0; top: 0; width: 100%; height: 53px; background: var(--green-top); }
  .age { position: absolute; right: 24px; top: 76px; font-family: "Nunito Sans", sans-serif; font-size: 42px; color: var(--green-brand); }
  .wordmark {
    position: absolute; left: 130px; top: 170px; width: 630px;
    font-family: "Marcellus", serif; font-size: 168px; line-height: 1;
    color: var(--green-brand); letter-spacing: 4px; text-align: center;
  }
  .info-band { position: absolute; left: 0; top: 451px; width: 100%; height: 173px; background: var(--green-dark); }
  .leaf-art {
    position: absolute; left: 4px; top: 244px; width: 306px; height: 296px;
    background: radial-gradient(closest-side, rgba(198,224,138,0.95) 0%, rgba(166,207,94,0.75) 50%, rgba(166,207,94,0) 100%);
  }
  .pill {
    position: absolute; left: 191px; top: 423px; width: 519px; height: 68px;
    border-radius: 34px; background: var(--green-pill);
    box-shadow: 0 3px 6px rgba(0,0,0,0.35);
    color: var(--white); font-size: 49px; line-height: 68px; text-align: center; padding-left: 24px;
    white-space: nowrap;
  }
  .origin { position: absolute; left: 0; top: 520px; width: 100%; text-align: center; color: var(--white); font-size: 31px; letter-spacing: 1px; }
  .claim { position: absolute; left: 0; top: 572px; width: 100%; text-align: center; color: var(--green-light); font-size: 34px; white-space: nowrap; }
  .rule { position: absolute; left: 0; top: 624px; width: 100%; height: 12px; background: linear-gradient(to right, #e8e8e8, #b5b5b5 50%, #e8e8e8); }
  .lower {
    position: absolute; left: 0; top: 636px; width: 100%; height: 564px;
    background: linear-gradient(to bottom, var(--green-light) 0%, #6aa142 40%, var(--green-deep) 70%, #4c7d39 100%);
  }
  .warning {
    position: absolute; left: 56px; top: 653px; width: 781px; height: 393px;
    background: var(--white); border: 6px solid var(--black);
    font-family: "Oswald", sans-serif; font-weight: 600; color: var(--black);
    font-size: 43px; line-height: 53px; text-align: center; padding-top: 14px;
    white-space: nowrap;
  }
  .warning p + p { margin-top: 11px; }
  .weight { position: absolute; left: 50px; top: 1078px; font-family: "Nunito Sans", sans-serif; font-size: 70px; color: var(--white); line-height: 1; }
  .cross { position: absolute; left: 654px; top: 1071px; width: 95px; height: 95px; }
  .strains { position: absolute; left: 785px; top: 1074px; list-style: none; }
  .strains li { display: flex; align-items: center; height: 30px; color: var(--white); font-size: 18px; }
  .strains li::before { content: ""; width: 18px; height: 18px; background: var(--white); border: 1.5px solid #1c1c1c; margin-right: 10px; }
</style>
</head>
<body>
<div class="bag">
  <div class="top-band"></div>
  <div class="age">18+</div>
  <div class="wordmark">PLOMU</div>
  <div class="info-band"></div>
  <div class="leaf-art" role="img" aria-label="Illustration of a green cannabis leaf"></div>
  <div class="pill">Medical Marijuana</div>
  <div class="origin">100% SCHWEIZER HANF</div>
  <div class="claim">Product auf pflanzlicher Basis ohne Tabak</div>
  <div class="rule"></div>
  <div class="lower"></div>
  <div class="warning">
    <p>Rauchen fügt ihnen und den Menschen in<br>ihrer Umgebung erheblichen Schaden zu.</p>
    <p>Fumer nuit Gravement à votre<br>santé et à celle de votre entourage.</p>
    <p>Il fumo danneggia gravemente<br>te e chi ti sta intorno.</p>
  </div>
  <div class="weight">10g</div>
  <svg class="cross" viewBox="0 0 95 95" aria-hidden="true">
    <path d="M28 0h39v28h28v39H67v28H28V67H0V28h28z" fill="var(--cross)"/>
  </svg>
  <ul class="strains">
    <li>INDICA</li>
    <li>SATIVA</li>
    <li>HYBRID</li>
  </ul>
</div>
</body>
</html>
```